An awsome Vento salt flyer!

We need a professional looking flyer for our mineralsalt product. Named "Vento salt" coming from Maras Peru from the "Terrazales". I have an example but it's not professional looking yet. I hope you can make an amazing flyer for us! valecrestafoods.com is our webpage.
Target Market(s)
Bio shoppers, natural food lovers, healty food lovers,
Industry/Entity Type
Food Store
Requirements
Nice to have
- We would like to have a really nice professionally looking flyer. For the common flyer sizes like DL and A5. I uploaded some bag pictures too. They will be improved soon but its nice to show the product as well. The pink and yellow colors we use in the logo and package would be nice as well.

```html
<!DOCTYPE html>
<html lang="nl">
<head>
<meta charset="utf-8">
<title>Vento zout flyer</title>
<link href="https://fonts.googleapis.com/css2?family=Quicksand:wght@300;400;500;600;700&display=swap" rel="stylesheet">
<style>
  :root{
    --pink:#e4168a;
    --gold:#e0a52a;
    --gold-text:#a8864a;
    --cream:rgba(250,236,205,0.78);
    --cream-solid:#f7ecd6;
    --sand-light:#eccf98;
    --sand-mid:#dcae6a;
    --sand-dark:#b98a4e;
    --rock:#8a6a52;
    --text-dark:#6b5536;
    --stage:#e9ecef;
  }
  *{box-sizing:border-box;margin:0;padding:0}
  html,body{width:1200px;height:1200px;overflow:hidden;background:var(--stage);font-family:"Quicksand",sans-serif}
  .canvas{position:relative;width:1200px;height:1200px}
  .flyer{position:absolute;left:210px;width:780px;height:552px;overflow:hidden;box-shadow:0 6px 20px rgba(0,0,0,.18)}
  .flyer--front{top:30px}
  .flyer--back{top:618px;background:var(--cream-solid)}

  /* front */
  .photo-salt-pans{position:absolute;inset:0;background:
      radial-gradient(ellipse at 70% 70%,#e9c17f 0%,transparent 55%),
      linear-gradient(160deg,#f1dcb0 0%,var(--sand-light) 35%,var(--sand-mid) 70%,var(--sand-dark) 100%)}
  .front-panel{position:absolute;left:30px;top:0;width:300px;height:100%;background:var(--cream)}
  .brand{position:absolute;left:0;width:300px;top:34px;display:flex;align-items:center;justify-content:center;gap:6px;font-weight:600;font-size:19px;color:var(--gold)}
  .brand-dot{width:10px;height:10px;border-radius:50%;background:var(--gold)}
  .title{position:absolute;left:58px;top:110px;font-weight:300;font-size:62px;letter-spacing:1px;color:var(--pink);line-height:1}
  .subtitle{position:absolute;left:60px;top:178px;font-size:17px;color:var(--gold-text);font-weight:400}
  .claim-band{position:absolute;left:50px;top:214px;width:380px;padding:10px 20px 12px;background:var(--pink);color:#fff}
  .claim-band .small{font-size:19px;font-weight:500;display:block}
  .claim-band .big{font-size:28px;font-weight:600;display:block;line-height:1.15}
  .benefits{position:absolute;left:60px;top:312px;width:330px;color:var(--gold-text);font-size:14px;font-weight:500;line-height:1.45}
  .benefits p{margin-bottom:2px}
  .benefits ul{list-style:none}
  .benefits li{display:flex;align-items:center;gap:6px}
  .tick{width:12px;height:12px;flex:none}

  /* back */
  .photo-salt-cave{position:absolute;left:0;top:0;width:390px;height:552px;background:linear-gradient(180deg,#7d6049 0%,#a98566 40%,#d7bb92 70%,#ecd6ad 100%)}
  .photo-salt-bowl{position:absolute;left:470px;top:0;width:240px;height:110px;border-radius:0 0 120px 120px;background:radial-gradient(circle at 50% 30%,#ffffff 0%,#efe9df 55%,#b9b4ad 100%)}
  .back-texture{position:absolute;left:390px;top:0;width:390px;height:552px;background:linear-gradient(180deg,#f6e7c9 0%,#f9efdc 60%,#efe2c8 100%)}
  .columns{position:absolute;left:405px;top:125px;width:360px;display:flex;gap:18px;color:var(--text-dark);font-size:10.5px;line-height:1.45}
  .col{flex:1}
  .col h3{color:var(--pink);font-size:12px;font-weight:700;margin-top:10px}
  .col h3:first-child{margin-top:0}
  .web{position:absolute;right:18px;bottom:14px;font-size:11px;font-weight:600;color:var(--pink)}
</style>
</head>
<body>
<div class="canvas">

  <section class="flyer flyer--front">
    <div class="photo-salt-pans" role="img" aria-label="Zoutpannen in de Terrazales met een zoutwerker die met de hand zout oogst"></div>
    <div class="front-panel"></div>
    <div class="brand"><span class="brand-dot"></span>Valecresta</div>
    <h1 class="title">VENTO ZOUT</h1>
    <p class="subtitle">uit de heilige vallei van de Incas</p>
    <div class="claim-band">
      <span class="small">Het meest zuivere en volledige</span>
      <span class="big">Mineraal Keukenzout</span>
    </div>
    <div class="benefits">
      <p>Bevat 84 mineralen en sporenelementen o.a. calcium, ijzer, zink, magnesium en voldoende jodium (3,5 mg/100gr)</p>
      <ul>
        <li><svg class="tick" viewBox="0 0 12 12"><path d="M1 6.5l3 3 7-8" fill="none" stroke="currentColor" stroke-width="1.8"/></svg>Heerlijk van smaak</li>
        <li><svg class="tick" viewBox="0 0 12 12"><path d="M1 6.5l3 3 7-8" fill="none" stroke="currentColor" stroke-width="1.8"/></svg>Minder natrium</li>
        <li><svg class="tick" viewBox="0 0 12 12"><path d="M1 6.5l3 3 7-8" fill="none" stroke="currentColor" stroke-width="1.8"/></svg>Natuurlijk proces van winning</li>
        <li><svg class="tick" viewBox="0 0 12 12"><path d="M1 6.5l3 3 7-8" fill="none" stroke="currentColor" stroke-width="1.8"/></svg>Afkomstig van een oude schone oceaan</li>
        <li><svg class="tick" viewBox="0 0 12 12"><path d="M1 6.5l3 3 7-8" fill="none" stroke="currentColor" stroke-width="1.8"/></svg>Met de hand geoogst</li>
        <li><svg class="tick" viewBox="0 0 12 12"><path d="M1 6.5l3 3 7-8" fill="none" stroke="currentColor" stroke-width="1.8"/></svg>100% eerlijk</li>
      </ul>
    </div>
  </section>

  <section class="flyer flyer--back">
    <div class="photo-salt-cave" role="img" aria-label="Zoutkristallen en zoutterrassen in de bergen van Maras"></div>
    <div class="back-texture" role="img" aria-label="Lichte achtergrond van zoutkristallen"></div>
    <div class="photo-salt-bowl" role="img" aria-label="Schaal met grof Vento zout"></div>
    <div class="columns">
      <div class="col">
        <h3>Herkomst</h3>
        <p>Het Vento zout wordt met de hand gewonnen in de Terrazales van Maras, Cusco, in Peru. Al eeuwenlang oogsten de lokale families het zout uit duizenden kleine zoutpannen op de berghelling.</p>
        <h3>Mineralen</h3>
        <p>Een natuurlijke bron in de berg voert zout water aan uit een oude oceaan. De zon droogt het water in de pannen, zodat een puur zout met 84 mineralen en sporenelementen achterblijft.</p>
      </div>
      <div class="col">
        <p>calcium, ijzer, magnesium en zink. Er zit minder natrium in dan in gewoon keukenzout. Ook dat maakt het een gezondere keuze.</p>
        <h3>Jodium</h3>
        <p>Het zout bevat van nature voldoende jodium, een mineraal dat ons lichaam nodig heeft. Veel natuurlijke zouten bevatten geen jodium; dit zout wel.</p>
        <h3>Eerlijke handel</h3>
        <p>Wij kopen direct bij de lokale bevolking in Peru voor een eerlijke prijs, zodat de opbrengst ook hen ten goede komt.</p>
        <h3>Aanbevolen</h3>
        <p>Ons team kent geen lekkerder zout dan het Vento zout. Het beste zout van de wereld!</p>
      </div>
    </div>
    <div class="web">valecrestafoods.com</div>
  </section>

</div>
</body>
</html>
```